Carpet cleaning company focused on high quality needs business cards

We are a growing company that just merged with another company and need to design a new business card. We do both residential as well as commercial cleaning. We do carpet, tile & grout, upholstery, hard floors, and stain & pet odor removal. We treat our customers like family and strive to achieve outstanding results with every job.

```html
<!DOCTYPE html>
<html lang="en">
<head>
<meta charset="utf-8">
<title>Hearthside – Business Cards</title>
<link href="https://fonts.googleapis.com/css2?family=Poppins:wght@400;500&family=Open+Sans:wght@600;700&display=swap" rel="stylesheet">
<style>
  :root {
    --backdrop: #b6b6b6;
    --brand-red: #ef4641;
    --paper-white: #ffffff;
    --cream: #fefde4;
    --ink: #1d1b1b;
    --shirt-blue: #1f84c4;
    --trouser-tan: #c39d5c;
  }
  * { margin: 0; padding: 0; box-sizing: border-box; }
  html, body {
    width: 1200px; height: 1200px; overflow: hidden;
    background: var(--backdrop);
    font-family: "Poppins", sans-serif;
  }
  .card {
    position: absolute; top: 305px;
    height: 597px; overflow: hidden;
  }
  .card-front { left: 202px; width: 371px; background: var(--brand-red); }
  .card-back { left: 603px; width: 366px; background: var(--brand-red); }
  .card-shape { position: absolute; inset: 0; width: 100%; height: 100%; }

  .tagline {
    position: absolute; top: 30px; left: 0; width: 100%;
    text-align: center; color: var(--paper-white);
    font-size: 16.5px; font-weight: 500; white-space: nowrap;
  }
  .mascot-slot { position: absolute; border-radius: 2px; }
  .front-mascot {
    left: 29px; top: 158px; width: 144px; height: 169px;
    background: linear-gradient(180deg, var(--paper-white) 0%, var(--shirt-blue) 45%, var(--brand-red) 75%);
  }
  .brand-name {
    position: absolute; left: 186px; top: 258px;
    font-family: "Open Sans", sans-serif; font-weight: 700;
    font-size: 26px; line-height: 32px; color: var(--ink);
    white-space: nowrap;
  }
  .service-list {
    position: absolute; top: 443px; left: 0; width: 100%;
    list-style: none; text-align: center; color: var(--paper-white);
    font-size: 17px; line-height: 24.8px; font-weight: 400;
  }

  .back-mascot {
    left: 47px; top: 29px; width: 244px; height: 347px;
    background: linear-gradient(180deg, var(--cream) 0%, var(--shirt-blue) 50%, var(--trouser-tan) 75%, var(--brand-red) 100%);
  }
  .holder-name {
    position: absolute; top: 403px; left: 0; width: 100%; text-align: center;
    font-family: "Open Sans", sans-serif; font-weight: 600;
    font-size: 24.5px; color: var(--paper-white); letter-spacing: -0.3px;
  }
  .holder-role {
    position: absolute; top: 431px; left: 0; width: 100%; text-align: center;
    font-size: 17.5px; color: var(--paper-white);
  }
  .contact-icons {
    position: absolute; top: 465px; left: 0; width: 100%;
    display: flex; justify-content: center; align-items: center; gap: 4px;
  }
  .contact-icons .rule { width: 52px; height: 1px; background: var(--paper-white); opacity: 0.8; margin: 0 4px; }
  .icon-box {
    width: 25px; height: 25px; background: var(--paper-white); border-radius: 3px;
    display: flex; align-items: center; justify-content: center;
  }
  .contact-lines {
    position: absolute; top: 497px; left: 0; width: 100%;
    list-style: none; text-align: center; color: var(--paper-white);
    font-size: 16.5px; line-height: 25px; white-space: nowrap;
  }
</style>
</head>
<body>

<section class="card card-front">
  <svg class="card-shape" viewBox="0 0 371 597" preserveAspectRatio="none" aria-hidden="true">
    <polygon points="0,106 371,66 371,414 0,414" fill="var(--paper-white)"/>
  </svg>
  <p class="tagline">RESIDENTIAL &amp; COMMERCIAL CLEANING</p>
  <div class="mascot-slot front-mascot" role="img" aria-label="Cartoon cleaner mascot raising a steam wand in front of a red sunburst panel"></div>
  <div class="brand-name">Hearthside</div>
  <ul class="service-list">
    <li>CARPET</li>
    <li>TILE &amp; GROUT</li>
    <li>UPHOLSTERY</li>
    <li>HARD FLOORS &amp; STAIN</li>
    <li>PET ODOR REMOVAL</li>
  </ul>
</section>

<section class="card card-back">
  <svg class="card-shape" viewBox="0 0 366 597" preserveAspectRatio="none" aria-hidden="true">
    <polygon points="0,0 366,0 366,182 0,295" fill="var(--cream)"/>
  </svg>
  <div class="mascot-slot back-mascot" role="img" aria-label="Large cartoon cleaner mascot holding a steam cleaning wand with hose, bursting rays behind him"></div>
  <p class="holder-name">DANIEL BROOKS</p>
  <p class="holder-role">Managing Director</p>
  <div class="contact-icons">
    <span class="rule"></span>
    <span class="icon-box" aria-label="phone">
      <svg width="15" height="15" viewBox="0 0 16 16"><path d="M2 6c0-2 3-3 6-3s6 1 6 3l-3 1-1-2H6L5 7 2 6zM4 8h8l1 5H3l1-5z" fill="var(--brand-red)"/></svg>
    </span>
    <span class="icon-box" aria-label="email">
      <svg width="15" height="15" viewBox="0 0 16 16"><rect x="1.5" y="3.5" width="13" height="9" fill="none" stroke="var(--brand-red)" stroke-width="1.4"/><path d="M1.5 3.5l6.5 5 6.5-5M1.5 12.5l5-4.5M14.5 12.5l-5-4.5" fill="none" stroke="var(--brand-red)" stroke-width="1.2"/></svg>
    </span>
    <span class="icon-box" aria-label="website">
      <svg width="15" height="15" viewBox="0 0 16 16"><circle cx="8" cy="8" r="6.5" fill="var(--brand-red)"/><path d="M5 4c2 1 1 3 3 3s1 3 0 4M10 3c0 2 2 2 3 3" fill="none" stroke="var(--paper-white)" stroke-width="1.2"/></svg>
    </span>
    <span class="rule"></span>
  </div>
  <ul class="contact-lines">
    <li>044-555 010 200</li>
    <li>info@hearthsidehome.com</li>
    <li>www.hearthsidehome.com</li>
  </ul>
</section>

</body>
</html>
```